Tovel & Associates - London New Letting and Property Management Company *

Tovel & Associates LTD is a new company based in London, and works with brand new residential property in the city centre.

We are aiming to have 1000 new properties a year.

We are looking for something modern and minimalistic :
Logo ,Monogram, Paper Head and Business Card.

Target Market(s)

Internation landlords

Industry/Entity Type

Real Estate

Logo Text

Tovel & Associates

Colors

Designer to choose colors to be used in the design.

Requirements
Nice to have
• A particular monogram with "TA"
Should not have
• Little House over the logo

```html
<!DOCTYPE html>
<html lang="en">
<head>
<meta charset="utf-8">
<title>Tovel &amp; Associates – Business Card</title>
<link href="https://fonts.googleapis.com/css2?family=Work+Sans:wght@400;500;600&display=swap" rel="stylesheet">
<style>
  :root {
    --stage: #1c1c1e;
    --card-dark: #151617;
    --card-light: #f2f2f2;
    --navy: #1b4e73;
    --sky: #29abe2;
    --ink-soft: #5f6266;
    --font: "Work Sans", Arial, sans-serif;
  }
  * { margin: 0; padding: 0; box-sizing: border-box; }
  html, body { width: 1200px; height: 900px; overflow: hidden; }
  body {
    background: var(--stage);
    font-family: var(--font);
    display: flex;
    flex-direction: column;
    align-items: center;
    justify-content: center;
    gap: 40px;
  }
  .card {
    width: 700px;
    height: 380px;
    position: relative;
    box-shadow: 0 12px 30px rgba(0,0,0,.45);
  }
  .card--back {
    background: var(--card-dark);
    display: flex;
    align-items: center;
    justify-content: center;
  }
  .card--front {
    background: var(--card-light);
    display: flex;
    align-items: center;
    padding: 0 60px 0 70px;
  }
  .brand {
    display: flex;
    flex-direction: column;
    align-items: center;
    gap: 18px;
  }
  .brand__square {
    width: 120px;
    height: 120px;
    background: var(--sky);
  }
  .brand__name {
    font-weight: 600;
    font-size: 17px;
    letter-spacing: 0.08em;
    text-transform: uppercase;
    color: var(--sky);
    white-space: nowrap;
  }
  .card--front .brand__square { background: var(--navy); width: 150px; height: 150px; }
  .card--front .brand__name { color: var(--navy); font-size: 16px; }
  .divider {
    width: 2px;
    height: 190px;
    background: var(--navy);
    margin: 0 48px 0 44px;
  }
  .contact { color: var(--ink-soft); }
  .contact__name {
    font-weight: 500;
    font-size: 30px;
    letter-spacing: 0.06em;
    color: var(--navy);
    text-transform: uppercase;
    line-height: 1;
  }
  .contact__role { font-size: 17px; margin: 6px 0 16px; }
  .contact__address { font-size: 17px; line-height: 1.3; margin-bottom: 14px; }
  .contact__list { list-style: none; font-size: 17px; line-height: 1.45; }
  .contact__list li { display: flex; align-items: center; gap: 10px; }
  .contact__list svg { width: 12px; height: 12px; flex: none; }
  .contact__web strong { font-weight: 500; color: var(--navy); }
</style>
</head>
<body>
  <section class="card card--back" aria-label="Card back">
    <div class="brand">
      <div class="brand__square"></div>
      <span class="brand__name">Tovel &amp; Associates</span>
    </div>
  </section>

  <section class="card card--front" aria-label="Card front">
    <div class="brand">
      <div class="brand__square"></div>
      <span class="brand__name">Tovel &amp; Associates</span>
    </div>
    <div class="divider"></div>
    <div class="contact">
      <h1 class="contact__name">Jonah Reeves</h1>
      <p class="contact__role">Director</p>
      <p class="contact__address">18 Calder Row<br>London EC2A 4NT</p>
      <ul class="contact__list">
        <li>
          <svg viewBox="0 0 12 12" aria-hidden="true"><path d="M3 1 L5 3.5 L4 5 Q5 7 7 8 L8.5 7 L11 9 L10 11 Q4 11 1 2 Z" fill="var(--navy)"/></svg>
          +44 20 7946 0312
        </li>
        <li>
          <svg viewBox="0 0 12 12" aria-hidden="true"><rect x="1" y="2.5" width="10" height="7" fill="none" stroke="var(--navy)" stroke-width="1.2"/><path d="M1 3 L6 7 L11 3" fill="none" stroke="var(--navy)" stroke-width="1.2"/></svg>
          info@tovelassociates.com
        </li>
        <li class="contact__web">
          <svg viewBox="0 0 12 12" aria-hidden="true"><circle cx="6" cy="6" r="5" fill="none" stroke="var(--navy)" stroke-width="1.1"/><ellipse cx="6" cy="6" rx="2.2" ry="5" fill="none" stroke="var(--navy)" stroke-width="1"/><path d="M1 6 H11" stroke="var(--navy)" stroke-width="1"/></svg>
          <span>www.<strong>tovelassociates</strong>.com</span>
        </li>
      </ul>
    </div>
  </section>
</body>
</html>
```